Website for a Psychologist in Private Practice

I need a cool web design for my website: www.drkalvoric.com. I would like it to look professional. Keep all the current content and add: Space for video; radio spots (see Silver Cedar Tunes Logo below for those); Quick Inquiry; Friendora link; 5 star rating on Rivo; a map; reviews from former patients. I am open to suggestions.

Target Market(s)

Those seeking individual and marital counseling.

Industry/Entity Type

Mental Health

Number of Pages Required

1 page

Font styles to use
Sans Serif
Other font styles liked:
• I'm open but no hard to read script

Requirements
Must have
• All the content on my home page with link for video and radio spots. List services and degrees and expertices (pics not necessary).
Nice to have
• A video of me and radio conversations (logo of Silver Cedar Tunes radio attached).
Should not have
• Cartoons, comedy, etc.... I don't need pictures of services (marital, depression, etc...) Just list those.

```html
<!DOCTYPE html>
<html lang="en">
<head>
<meta charset="utf-8">
<title>Dr. Mira K. Kalvoric – Individual and Marital Counseling</title>
<link rel="stylesheet" href="https://fonts.googleapis.com/css2?family=Lato:wght@400;700;900&family=Playball&display=swap">
<style>
:root{
  --blue:#2b84c4;
  --blue-dark:#1f6ea8;
  --gold:#c8b15a;
  --gold-band:#cdb668;
  --ink:#222;
  --text:#333;
  --muted:#888;
  --nav:#333333;
  --card:#e6e6e6;
  --light:#f4f4f4;
  --footer:#2b2b2b;
}
*{box-sizing:border-box;margin:0;padding:0}
html,body{width:1200px;height:2667px;overflow:hidden}
body{position:relative;background:#fff;font-family:"Lato",Arial,sans-serif;color:var(--text)}
.abs{position:absolute}
.script{font-family:"Playball",cursive;font-weight:400}

/* header */
.site-header{position:absolute;left:0;top:0;width:1200px;height:115px;background:#fbfbfb}
.brand{left:78px;top:44px;font-size:32px;font-weight:700;color:var(--gold);letter-spacing:.5px}
.contact-pill{top:39px;height:43px;border:1px solid #ddd;border-radius:22px;background:#fff;display:flex;align-items:center;gap:10px;padding-left:26px;font-size:16px;color:#444}
.contact-pill strong{color:#222;font-weight:700}
.pill-email{left:569px;width:306px}
.pill-call{left:887px;width:233px}

/* nav */
.main-nav{position:absolute;left:0;top:115px;width:1200px;height:61px;background:var(--nav)}
.main-nav a{position:absolute;top:0;height:61px;line-height:61px;color:#fff;text-decoration:none;font-size:18px;font-weight:700;transform:translateX(-50%);white-space:nowrap}
.main-nav a.active{top:11px;height:40px;line-height:40px;background:var(--blue);padding:0 10px;left:116px}

/* hero */
.hero{position:absolute;left:0;top:176px;width:1200px;height:487px;
  background:radial-gradient(ellipse at 68% 55%,#a9b468 0%,#7f9a45 30%,#5d7f2f 60%,#3f5f22 100%)}
.hero h1{left:82px;top:176px;font-size:27px;line-height:38px;font-weight:700;color:#fff;letter-spacing:.3px}
.btn-outline-blue{left:80px;top:272px;width:181px;height:37px;background:var(--blue);border:2px solid #fff;color:#fff;font-weight:700;font-size:19px;text-align:center;line-height:33px}
.slide-arrow{top:190px;width:40px;height:34px;background:#2f2f2f;display:flex;align-items:center;justify-content:center}
.slide-arrow.prev{left:0}
.slide-arrow.next{right:0}

/* about */
.about{position:absolute;left:0;top:663px;width:1200px;height:489px;background:#fff}
.section-title{font-size:40px;color:var(--ink);white-space:nowrap}
.section-title span{color:var(--gold)}
.about .section-title{left:80px;top:70px}
.rule{height:3px;background:var(--blue)}
.about .rule{left:82px;top:130px;width:103px}
.about-text{left:82px;top:153px;width:680px;font-size:14.5px;line-height:26px;color:#333}
.about-text b{color:#222}
.pillar{top:270px;display:flex;gap:14px}
.pillar-icon{width:78px;height:78px;border:2px solid var(--blue);border-radius:50%;display:flex;align-items:center;justify-content:center;flex:none}
.pillar h3{font-size:21px;font-weight:400;color:var(--blue);margin-top:10px;padding-bottom:3px;border-bottom:1px dashed #ccc;display:inline-block}
.pillar p{font-size:14.5px;line-height:20px;color:#333;margin-top:6px;width:270px}

.inquiry{left:807px;top:80px;width:313px;height:331px;background:#eeeeee;border-radius:4px}
.inquiry-head{height:47px;background:var(--blue);border-radius:4px 4px 0 0;color:#fff;font-weight:700;font-size:20px;line-height:47px;padding-left:25px}
.field{position:absolute;left:23px;width:267px;height:35px;background:#fff;border:1px solid #d6d6d6;font-size:13px;color:#777;padding:9px 10px}
.field.area{height:67px}
.submit{position:absolute;left:25px;top:277px;width:94px;height:40px;background:var(--blue);color:#fff;font-weight:700;font-size:16px;text-align:center;line-height:40px;border-radius:2px}

/* sessions + video */
.sessions{position:absolute;left:0;top:1152px;width:1200px;height:356px;display:flex}
.sessions-panel{position:relative;width:600px;height:356px;background:linear-gradient(160deg,#d7c174 0%,#c9b066 55%,#bba35a 100%)}
.video-panel{position:relative;width:600px;height:356px;background:linear-gradient(200deg,#6aa6d6 0%,#4c92cc 50%,#3f86c2 100%)}
.sessions-panel h2{position:absolute;left:0;width:600px;top:100px;text-align:center;color:#fff;font-size:33px;font-weight:700}
.session-list{position:absolute;top:155px;list-style:none}
.session-list li{height:30px;display:flex;align-items:center;gap:8px;font-size:14px;color:#222;font-weight:700}
.btn-outline-white{position:absolute;left:260px;top:290px;width:160px;height:37px;border:2px solid #fff;color:#fff;font-size:18px;font-weight:700;text-align:center;line-height:33px}
.video-panel p{position:absolute;left:0;width:600px;top:110px;text-align:center;color:#fff;font-size:18px}
.play{position:absolute;left:232px;top:165px;width:57px;height:42px;background:#fff;border-radius:8px;display:flex;align-items:center;justify-content:center}
.video-panel h4{position:absolute;left:0;width:522px;top:240px;text-align:center;color:#fff;font-size:18px;font-weight:700}

/* expertise */
.expertise{position:absolute;left:0;top:1508px;width:1200px;height:652px;background:#fff}
.expertise .section-title{left:0;width:1200px;text-align:center;top:45px}
.centered-rule{left:548px;width:106px}
.expertise .centered-rule{top:104px}
.card{width:252px;height:217px;background:linear-gradient(135deg,#e4e4e4 0%,#e4e4e4 45%,#ececec 45%,#ececec 70%,#e4e4e4 70%);overflow:hidden;text-align:center}
.card-icon{height:60px;margin-top:22px;display:flex;align-items:center;justify-content:center}
.card h3{margin-top:22px;font-size:15px;font-weight:700;color:#222}
.card p{margin-top:12px;font-size:13.5px;line-height:19px;color:#333;padding:0 22px}
.card .corner{position:absolute;right:0;bottom:0;width:0;height:0;border-left:36px solid transparent;border-bottom:36px solid var(--gold)}
.card .plus{position:absolute;right:5px;bottom:2px;color:#fff;font-size:12px;font-weight:700}

/* radio */
.radio{position:absolute;left:0;top:2160px;width:1200px;height:293px;background:var(--light)}
.radio .section-title{left:0;width:1200px;text-align:center;top:42px}
.radio .centered-rule{top:100px}
.quote{left:160px;width:880px;top:127px;text-align:center;font-style:italic;font-size:14px;line-height:23px;color:#333}
.quote-mark{color:var(--gold);font-size:34px;font-style:normal;font-weight:900;vertical-align:-10px;margin-right:6px}
.quote-name{left:0;width:1200px;top:212px;text-align:center;color:var(--gold);font-size:17px;font-weight:700}
.radio-arrow{top:135px}

/* footer */
.site-footer{position:absolute;left:0;top:2453px;width:1200px;height:178px;background:linear-gradient(180deg,#2e2e2e,#262626)}
.donate{left:350px;top:32px;font-size:17px;font-weight:700;color:#fff}
.badge{top:23px;width:88px;height:40px;background:#fff;border-radius:3px}
.footer-item{top:110px;display:flex;align-items:center;gap:12px;color:#fff;font-size:14px}
.copyright{position:absolute;left:0;top:2631px;width:1200px;height:36px;background:var(--blue);color:#fff;font-size:13px;text-align:center;line-height:36px}
</style>
</head>
<body>

<header class="site-header">
  <div class="abs brand">Dr. Mira K. Kalvoric</div>
  <div class="abs contact-pill pill-email">
    <svg width="18" height="14" viewBox="0 0 18 14"><rect x="1" y="1" width="16" height="12" fill="none" stroke="#c8b15a" stroke-width="1.6"/><path d="M1 1l8 7 8-7" fill="none" stroke="#c8b15a" stroke-width="1.6"/></svg>
    <span>Email Us <strong>mk@drkalvoric.com</strong></span>
  </div>
  <div class="abs contact-pill pill-call">
    <svg width="17" height="17" viewBox="0 0 24 24"><path d="M6.6 10.8a15 15 0 006.6 6.6l2.2-2.2a1 1 0 011-.25 11.4 11.4 0 003.6.57 1 1 0 011 1V20a1 1 0 01-1 1A17 17 0 013 4a1 1 0 011-1h3.5a1 1 0 011 1 11.4 11.4 0 00.57 3.6 1 1 0 01-.25 1z" fill="none" stroke="#c8b15a" stroke-width="1.6"/></svg>
    <span>Call Us <strong>(949) 555 0182</strong></span>
  </div>
</header>

<nav class="main-nav">
  <a class="active" href="#">HOME</a>
  <a href="#" style="left:267px">BIO</a>
  <a href="#" style="left:448px">MY EXPERTISE</a>
  <a href="#" style="left:653px">SESSIONS</a>
  <a href="#" style="left:848px">RESOURCES</a>
  <a href="#" style="left:1061px">CONTACT ME</a>
</nav>

<section class="hero" role="img" aria-label="Photo of a woman outdoors in a green park, arms spread wide in relief">
  <h1 class="abs">I PROVIDE INDIVIDUAL AND<br>MARITAL COUNSELING</h1>
  <div class="abs btn-outline-blue">Get Started</div>
  <div class="abs slide-arrow prev"><svg width="10" height="14" viewBox="0 0 10 14"><path d="M8 1L2 7l6 6" fill="none" stroke="#fff" stroke-width="2.4"/></svg></div>
  <div class="abs slide-arrow next"><svg width="10" height="14" viewBox="0 0 10 14"><path d="M2 1l6 6-6 6" fill="none" stroke="#fff" stroke-width="2.4"/></svg></div>
</section>

<section class="about">
  <h2 class="abs section-title script">About <span>Dr. Mira K. Kalvoric</span></h2>
  <div class="abs rule"></div>
  <p class="abs about-text">While I acknowledge the importance of my education, I also appreciate the role my experiences have played in allowing me to relate so well to others. Allow me to share those I feel are most relevant with you.I survived an abusive childhood that my mother and sister unfortunately did not &nbsp;……. <b>Read More</b></p>

  <div class="abs pillar" style="left:80px">
    <div class="pillar-icon">
      <svg width="42" height="42" viewBox="0 0 42 42"><path d="M10 38V29c-4-3-6-7-6-12C4 9 11 3 20 3s16 6 16 14l3 7-4 1v6c0 2-2 3-4 3h-4v4z" fill="#c8b15a"/><circle cx="21" cy="17" r="6" fill="#fff"/><circle cx="21" cy="17" r="3" fill="#c8b15a"/></svg>
    </div>
    <div><h3>My Philosophy</h3><p>Lorem ipsum dolor sit amet,conse ctetuer adipiscing elit,</p></div>
  </div>
  <div class="abs pillar" style="left:452px">
    <div class="pillar-icon">
      <svg width="44" height="44" viewBox="0 0 44 44"><circle cx="20" cy="24" r="16" fill="none" stroke="#c8b15a" stroke-width="4"/><circle cx="20" cy="24" r="9" fill="none" stroke="#2b84c4" stroke-width="4"/><circle cx="20" cy="24" r="3" fill="#c8b15a"/><path d="M20 24L38 6" stroke="#222" stroke-width="2.5"/><path d="M34 4l6 0-2 6z" fill="#222"/></svg>
    </div>
    <div><h3>My Mission</h3><p>Lorem ipsum dolor sit amet,conse ctetuer adipiscing elit,</p></div>
  </div>

  <form class="abs inquiry">
    <div class="inquiry-head">QUICK INQUIRY</div>
    <div class="field" style="top:66px">Full Name</div>
    <div class="field" style="top:107px">Phone Number</div>
    <div class="field" style="top:149px">Email
      <svg style="position:absolute;right:10px;top:13px" width="11" height="8" viewBox="0 0 11 8"><path d="M0 0h11L5.5 8z" fill="#c8b15a"/></svg>
    </div>
    <div class="field area" style="top:191px">Message</div>
    <div class="submit">SUBMIT</div>
  </form>
</section>

<section class="sessions">
  <div class="sessions-panel" role="img" aria-label="Gold-toned photo of a counseling session at a desk">
    <svg style="position:absolute;left:280px;top:30px" width="52" height="52" viewBox="0 0 52 52"><circle cx="20" cy="11" r="9" fill="#fff"/><path d="M4 48V34c0-8 6-12 16-12 4 0 7 1 9 2l-5 14H4z" fill="#fff"/><rect x="28" y="24" width="18" height="22" rx="2" fill="none" stroke="#fff" stroke-width="3"/><path d="M32 34l4 4 8-10" fill="none" stroke="#fff" stroke-width="3"/></svg>
    <h2>Type of Sessions i Provide</h2>
    <ul class="session-list" style="left:156px">
      <li><svg width="14" height="11" viewBox="0 0 14 11"><path d="M1 5l4 4 8-8" fill="none" stroke="#222" stroke-width="2"/></svg>Individual Sessions</li>
      <li><svg width="14" height="11" viewBox="0 0 14 11"><path d="M1 5l4 4 8-8" fill="none" stroke="#222" stroke-width="2"/></svg>Marriage Sessions</li>
      <li><svg width="14" height="11" viewBox="0 0 14 11"><path d="M1 5l4 4 8-8" fill="none" stroke="#222" stroke-width="2"/></svg>Family Sessions</li>
      <li><svg width="14" height="11" viewBox="0 0 14 11"><path d="M1 5l4 4 8-8" fill="none" stroke="#222" stroke-width="2"/></svg>Phone Sessions</li>
    </ul>
    <ul class="session-list" style="left:316px">
      <li><svg width="14" height="11" viewBox="0 0 14 11"><path d="M1 5l4 4 8-8" fill="none" stroke="#222" stroke-width="2"/></svg>Divorce Mediation</li>
      <li><svg width="14" height="11" viewBox="0 0 14 11"><path d="M1 5l4 4 8-8" fill="none" stroke="#222" stroke-width="2"/></svg>Custody Evaluation Sessions</li>
      <li><svg width="14" height="11" viewBox="0 0 14 11"><path d="M1 5l4 4 8-8" fill="none" stroke="#222" stroke-width="2"/></svg>Testing Sessions</li>
      <li><svg width="14" height="11" viewBox="0 0 14 11"><path d="M1 5l4 4 8-8" fill="none" stroke="#222" stroke-width="2"/></svg>Weekend / Holiday Sessions</li>
    </ul>
    <div class="btn-outline-white">Get Started</div>
  </div>
  <div class="video-panel" role="img" aria-label="Blue-toned video still of a counseling conversation">
    <p>Lorem ipsum dolor sit amet, consectetu</p>
    <div class="play"><svg width="16" height="18" viewBox="0 0 16 18"><path d="M1 1l14 8-14 8z" fill="#4c92cc"/></svg></div>
    <h4>WATCH VIDEO</h4>
  </div>
</section>

<section class="expertise">
  <h2 class="abs section-title script">My <span>Expertise</span></h2>
  <div class="abs rule centered-rule"></div>

  <div class="abs card" style="left:80px;top:145px">
    <div class="card-icon"><svg width="54" height="50" viewBox="0 0 54 50"><path d="M27 48L5 26C-2 18 3 3 15 3c6 0 10 4 12 7 2-3 6-7 12-7 12 0 17 15 10 23z" fill="#222"/><path d="M24 14l6 8-8 6 6 8" fill="none" stroke="#e4e4e4" stroke-width="3"/></svg></div>
    <h3>DATING</h3><p>Lorem ipsum dolor sit amet, consectetuer adipiscing elit, sed diam nonummy nibh</p>
    <div class="corner"></div><span class="plus">+</span>
  </div>
  <div class="abs card" style="left:343px;top:145px">
    <div class="card-icon"><svg width="50" height="52" viewBox="0 0 50 52"><circle cx="15" cy="7" r="5" fill="#222"/><circle cx="35" cy="7" r="5" fill="#222"/><path d="M9 14h12l5 22h-7v14h-6V36H6z" fill="#222"/><rect x="29" y="14" width="12" height="20" fill="#222"/><rect x="30" y="34" width="4" height="16" fill="#222"/><rect x="36" y="34" width="4" height="16" fill="#222"/></svg></div>
    <h3>MARRIAGE</h3><p>Lorem ipsum dolor sit amet, consectetuer adipiscing elit, sed diam nonummy nibh</p>
    <div class="corner"></div><span class="plus">+</span>
  </div>
  <div class="abs card" style="left:606px;top:145px">
    <div class="card-icon"><svg width="54" height="52" viewBox="0 0 54 52"><rect x="16" y="3" width="34" height="26" fill="none" stroke="#222" stroke-width="4"/><circle cx="9" cy="14" r="6" fill="#222"/><path d="M2 50V24h14l12-6 2 4-12 9v19z" fill="#222"/><path d="M38 29v20M28 49h20" stroke="#222" stroke-width="3"/></svg></div>
    <h3>PARENTING &amp; PROFESSIONAL</h3><p>Lorem ipsum dolor sit amet, consectetuer adipiscing elit, sed diam nonummy nibh</p>
    <div class="corner"></div><span class="plus">+</span>
  </div>
  <div class="abs card" style="left:869px;top:145px">
    <div class="card-icon"><svg width="54" height="50" viewBox="0 0 54 50"><circle cx="14" cy="9" r="7" fill="#222"/><circle cx="40" cy="9" r="7" fill="#222"/><path d="M2 48c0-14 5-22 12-22s12 8 12 22z" fill="#222"/><path d="M28 48c0-14 5-22 12-22s12 8 12 22z" fill="#222"/><path d="M18 38h18M32 34l4 4-4 4" fill="none" stroke="#e4e4e4" stroke-width="2.5"/></svg></div>
    <h3>RELATIONSHIPS</h3><p>Lorem ipsum dolor sit amet, consectetuer adipiscing elit, sed diam nonummy nibh</p>
    <div class="corner"></div><span class="plus">+</span>
  </div>

  <div class="abs card" style="left:80px;top:376px">
    <div class="card-icon"><svg width="44" height="50" viewBox="0 0 44 50"><circle cx="26" cy="7" r="6" fill="#222"/><path d="M14 18l14-3 4 16-10 2 4 15h-6l-5-18 6-3-3-6-6 8-5-3z" fill="#222"/></svg></div>
    <h3>DEPRESSION &amp; ANXIETY ISSUES</h3><p>Lorem ipsum dolor sit amet, consectetuer adipiscing elit, sed diam nonummy nibh</p>
    <div class="corner"></div><span class="plus">+</span>
  </div>
  <div class="abs card" style="left:343px;top:376px">
    <div class="card-icon"><svg width="60" height="44" viewBox="0 0 60 44"><path d="M2 4c8 4 18 4 26 0v14c0 10-6 16-13 16S2 28 2 18z" fill="#222"/><path d="M32 10c8 4 18 4 26 0v14c0 10-6 16-13 16s-13-6-13-16z" fill="#222"/><path d="M8 14h6M18 14h6M10 24c3-3 7-3 10 0M38 20h6M48 20h6M40 28c3 3 7 3 10 0" stroke="#e4e4e4" stroke-width="2.5" fill="none"/></svg></div>
    <h3>PERSONALITY DISORDERS</h3><p>Lorem ipsum dolor sit amet, consectetuer adipiscing elit, sed diam nonummy nibh</p>
    <div class="corner"></div><span class="plus">+</span>
  </div>
  <div class="abs card" style="left:606px;top:376px">
    <div class="card-icon"><svg width="52" height="52" viewBox="0 0 52 52"><path d="M26 4v40M14 48h24M8 12h36" stroke="#222" stroke-width="3.5"/><path d="M8 12L2 28h12zM44 12l-6 16h12z" fill="none" stroke="#222" stroke-width="2.5"/><path d="M2 28a6 4 0 0012 0zM38 28a6 4 0 0012 0z" fill="#222"/></svg></div>
    <h3>DIVORCE MEDIATION</h3><p>Lorem ipsum dolor sit amet, consectetuer adipiscing elit, sed diam nonummy nibh</p>
    <div class="corner"></div><span class="plus">+</span>
  </div>
  <div class="abs card" style="left:869px;top:376px">
    <div class="card-icon"><svg width="52" height="52" viewBox="0 0 52 52"><circle cx="26" cy="22" r="7" fill="#222"/><path d="M12 50c0-12 6-18 14-18s14 6 14 18z" fill="#222"/><circle cx="10" cy="10" r="4" fill="#222"/><rect x="22" y="1" width="8" height="8" fill="#222"/><path d="M42 6l5 8h-10z" fill="#222"/><circle cx="6" cy="24" r="3" fill="#222"/><circle cx="46" cy="24" r="3" fill="#222"/></svg></div>
    <h3>LIFE MANAGEMENT</h3><p>Lorem ipsum dolor sit amet, consectetuer adipiscing elit, sed diam nonummy nibh</p>
    <div class="corner"></div><span class="plus">+</span>
  </div>
</section>

<section class="radio">
  <h2 class="abs section-title script">Radio <span>Conversations</span></h2>
  <div class="abs rule centered-rule"></div>
  <svg class="abs radio-arrow" style="left:76px" width="12" height="20" viewBox="0 0 12 20"><path d="M10 2L2 10l8 8" fill="none" stroke="#aaa" stroke-width="2"/></svg>
  <svg class="abs radio-arrow" style="left:1112px" width="12" height="20" viewBox="0 0 12 20"><path d="M2 2l8 8-8 8" fill="none" stroke="#aaa" stroke-width="2"/></svg>
  <p class="abs quote"><span class="quote-mark">&ldquo;</span>Lorem ipsum dolor sit amet, consectetuer adipiscing elit, sed diam nonummy nibh euismod tincidunt ut laoreet dolore magna aliquam erat volutpat. Ut wisi enim ad minim veniam, quis nostrud exerci tation ullamcorper suscipit lobortis nisl ut aliquip ex ea commodo consequat. Duis autem vel eum iriure.</p>
  <div class="abs quote-name">Alan Whitford</div>
</section>

<footer class="site-footer" role="img" aria-label="Dark street map of the office neighbourhood">
  <div class="abs donate">A portion of all revenue is donated to</div>
  <div class="abs badge" style="left:651px"></div>
  <div class="abs badge" style="left:745px"></div>
  <div class="abs footer-item" style="left:183px">
    <svg width="18" height="24" viewBox="0 0 18 24"><path d="M9 23S1 13 1 8.5a8 8 0 0116 0C17 13 9 23 9 23z" fill="#fff"/><circle cx="9" cy="8.5" r="3" fill="#2b2b2b"/></svg>
    <span>418 Harbor Lane, Suite 210 Coastview, CA 92600</span>
  </div>
  <div class="abs footer-item" style="left:630px">
    <svg width="16" height="20" viewBox="0 0 16 20"><path d="M3 1h4l1 5-3 2c1 3 2 5 4 6l2-3 4 2v4c-1 2-3 2-5 1C5 15 1 9 1 4c0-2 1-3 2-3z" fill="#fff"/></svg>
    <span>(949) 555 0182</span>
  </div>
  <div class="abs footer-item" style="left:832px">
    <svg width="22" height="15" viewBox="0 0 22 15"><rect width="22" height="15" fill="#fff"/><path d="M1 1l10 8 10-8" fill="none" stroke="#2b2b2b" stroke-width="1.6"/></svg>
    <span>mk@drkalvoric.com</span>
  </div>
</footer>
<div class="copyright">Copyright 2016 Dr. Mira K. Kalvoric. All Right Reserved</div>

</body>
</html>
```